Very dated, simple professional product website needs updating/reskinning of template

Our client currently has a very simple website at www.brightpitch4homes.example that is very, very dated, uses flash, and the template needs to have an updated look for 2014. It needs to look professional, corporate, strong colors, and if using images, actors must have a very well dressed look, etc. Client likes the layout (but not necessarily the colors, etc.) of another similar product site, www.deedcraftkit.example, for example.

The Keystoner product is an online "presentation document builder" that uses up-to-date content for agents to create 20 - 40 page presentations for potential clients. Real estate agents pay $500+ one-time plus $85/year to use the service, so the website look needs to be consistent with a $500+ product. All of the content will stay essentially the same for now: the goal is to simply re-skin the site to make it look modern, ideally through the use of new CSS files and images, and maybe some script. But we do not want to recode the whole thing, just update the template.

The site layout also needs to work with mobile devices, and so the flash has to be removed, but there is still a need to have possibly a slideshow or something to quickly grab the attention of people who visit the site so they can very quickly understand what the product is.

Also, the plan is to cut down on some of the menu buttons and/or rename them to be more compelling. There are pages on the site that can only be viewed after logging in, and we will want to use the template for those secure pages also.

Project Deadline Extended
Reason: My clients have requested that we see if we can get a few more designs to choose between, and to provide them with some time to mull over the current designs.

Project Deadline Extended
Reason: My client has requested that we continue to seek designs.

Industry/Entity Type

Product

```html
<!DOCTYPE html>
<html lang="en">
<head>
<meta charset="utf-8">
<title>Keystoner – Real Estate Presentations</title>
<link rel="stylesheet" href="https://fonts.googleapis.com/css2?family=Roboto+Condensed:wght@400;700&family=Signika:wght@300;400;600&family=Open+Sans:wght@400;600;700&display=swap">
<style>
:root{
  --orange:#f5a400;
  --orange-text:#e89c00;
  --more-orange:#e07b00;
  --more-green:#5b8c0a;
  --dark:#2e2e2e;
  --darker:#1f1f1f;
  --page:#e8e8e8;
  --white:#ffffff;
  --text:#333333;
  --muted:#cccccc;
  --rule:#4a4a4a;
  --blue:#1a9de2;
}
*{margin:0;padding:0;box-sizing:border-box}
html,body{width:972px;height:1200px;overflow:hidden}
body{position:relative;background:var(--page);font-family:"Open Sans",sans-serif;color:var(--text)}
.abs{position:absolute}

/* top navigation */
.top-nav{left:0;top:0;width:972px;height:39px;background:linear-gradient(#3a3a3a,#262626);border-bottom:2px solid #bdbdbd;z-index:3}
.top-nav a{position:absolute;top:12px;font:400 13px/1 "Roboto Condensed",sans-serif;color:#f2f2f2;text-decoration:none}
.top-nav .sep{position:absolute;top:9px;width:1px;height:22px;background:#4d4d4d}
.top-nav .active-bar{position:absolute;left:251px;top:37px;width:107px;height:3px;background:var(--orange)}

/* hero */
.hero{left:0;top:39px;width:972px;height:458px;overflow:hidden}
.hero svg{position:absolute;left:0;top:0}
.hero-photo{position:absolute;left:0;top:0;width:972px;height:458px;background:linear-gradient(180deg,#b8c4cf 0%,#d9d2c2 30%,#e2d6bc 55%,#a9a08a 78%,#4f5a3a 100%)}
.brand-name{left:83px;top:58px;z-index:2;font:600 42px/1 "Signika",sans-serif;color:var(--white)}
.phone{left:735px;top:57px;z-index:2;display:flex;align-items:center;gap:12px;font:300 20px/1 "Signika",sans-serif;color:var(--white)}
.caption-bar{left:0;top:454px;width:972px;height:43px;background:rgba(40,40,40,.72);z-index:2}
.caption{left:84px;top:463px;z-index:3;font:400 20px/1 "Signika",sans-serif;color:var(--white);letter-spacing:.6px}
.dot{top:467px;width:17px;height:17px;border-radius:50%;border:2px solid #222;background:var(--white);z-index:3}
.dot.on{background:var(--orange)}

/* feature panel */
.panel{left:83px;top:529px;width:806px;height:311px;background:var(--white);border-radius:4px}
.feature{position:absolute;top:0;width:250px}
.feature h2{position:absolute;top:17px;font:600 19.5px/1 "Signika",sans-serif;color:var(--orange-text);white-space:nowrap}
.feature .thumb{position:absolute;top:51px;left:0;width:224px;height:75px;border:1px solid #c9c9c9}
.feature .intro{position:absolute;top:139px;left:2px;width:250px;font:700 8.6px/14px "Open Sans",sans-serif;color:#333}
.feature ul{position:absolute;top:173px;left:2px;list-style:none}
.feature li{font:400 10px/17px "Open Sans",sans-serif;color:#333;padding-left:9px;position:relative}
.feature li::before{content:"›";position:absolute;left:0;top:0;font-weight:700;color:#666}
.feature .more{position:absolute;top:274px;left:1px;width:250px;display:flex;align-items:center;font:700 9px/1 "Open Sans",sans-serif}
.feature .more::before{content:"";flex:1;height:1px;background:#d6d6d6;margin-right:4px}
.feature .more::after{content:"";width:26px;height:1px;background:#d6d6d6;margin-left:5px}
.more.orange{color:var(--more-orange)}
.more.green{color:var(--more-green)}

/* footer */
.footer{left:0;top:873px;width:972px;height:293px;background:var(--dark)}
.col-title{font:400 18.5px/1 "Roboto Condensed",sans-serif;color:#f0f0f0}
.col-rule{height:1px;background:var(--rule)}
.vrule{width:1px;background:#444}
.quote-text{left:99px;top:930px;width:160px;font:400 10px/17px "Open Sans",sans-serif;color:var(--muted);white-space:nowrap}
.qmark{font:700 30px/10px Georgia,serif;color:#6a6a6a;vertical-align:-10px}
.qmark.open{margin-right:3px}
.qmark.close{margin-left:12px}
.map-text{left:300px;top:928px;font:400 10.2px/17.5px "Open Sans",sans-serif;color:#dddddd;white-space:nowrap}
.map{left:309px;top:974px;width:317px;height:166px;background:linear-gradient(135deg,#eae6dc,#f1eadb 45%,#dfe8d2)}
.field{left:682px;width:174px;height:19px;border:1px solid #4c4c4c;background:#2b2b2b;font:400 9.5px/17px "Open Sans",sans-serif;color:#bbbbbb;padding-left:7px}
.submit{left:809px;top:1041px;width:47px;height:19px;background:var(--blue);border-radius:2px;font:700 10px/19px "Open Sans",sans-serif;color:var(--white);text-align:center}
.address{left:673px;top:1078px;font:600 8.7px/14.5px "Open Sans",sans-serif;color:#eeeeee}
.address b{color:var(--blue)}
.world{left:778px;top:1077px;width:78px;height:39px;background:radial-gradient(ellipse at center,#8c8c8c 0%,#6a6a6a 60%,transparent 72%)}

.bottom-nav{left:0;top:1166px;width:972px;height:34px;background:var(--darker);display:flex;align-items:center;padding-left:87px;gap:13px;font:400 11.5px/1 "Roboto Condensed",sans-serif;color:#eeeeee}
</style>
</head>
<body>

<nav class="top-nav abs">
  <a style="left:96px">Home</a><span class="sep" style="left:149px"></span>
  <a style="left:167px">About Us</a><span class="sep" style="left:232px"></span>
  <a style="left:254px">Getting The Business</a><span class="sep" style="left:378px"></span>
  <a style="left:398px">What is Keystoner</a><span class="sep" style="left:509px"></span>
  <a style="left:531px">Peer Reviews</a><span class="sep" style="left:618px"></span>
  <a style="left:638px">FAQ</a><span class="sep" style="left:679px"></span>
  <a style="left:701px">Contact Us</a>
  <span class="active-bar"></span>
</nav>

<header class="hero abs">
  <div class="hero-photo" role="img" aria-label="Photo of a row of cream-sided two-storey townhouses with grey roofs under a clear sky"></div>
  <svg width="972" height="458" viewBox="0 0 972 458" aria-hidden="true">
    <defs>
      <linearGradient id="headerShade" x1="0" y1="0" x2="0" y2="1">
        <stop offset="0" stop-color="#222"/>
        <stop offset="1" stop-color="#4a4a4a"/>
      </linearGradient>
    </defs>
    <path d="M0 0H972V100C900 60 780 50 640 72C460 100 320 124 200 112C110 103 50 88 0 72Z" fill="url(#headerShade)"/>
    <path d="M0 72C50 88 110 103 200 112C320 124 460 100 640 72C780 50 900 60 972 100V124C900 80 790 78 640 92C470 108 330 126 220 116C120 108 50 96 0 88Z" fill="#f5a400"/>
  </svg>
</header>
<div class="brand-name abs">Keystoner</div>
<div class="phone abs">
  <svg width="22" height="22" viewBox="0 0 22 22" aria-hidden="true">
    <path d="M3 2h4v18H3c-1 0-2-1-2-2V4c0-1 1-2 2-2z" fill="#fff"/>
    <rect x="8" y="4" width="12" height="16" rx="2" fill="none" stroke="#fff" stroke-width="2"/>
    <rect x="11" y="7" width="6" height="3" fill="#fff"/>
    <g fill="#fff"><rect x="11" y="12" width="2" height="2"/><rect x="15" y="12" width="2" height="2"/><rect x="11" y="15" width="2" height="2"/><rect x="15" y="15" width="2" height="2"/></g>
  </svg>
  <span>555 014 2290</span>
</div>
<div class="caption-bar abs"></div>
<div class="caption abs">Where Great Presentations Begin.</div>
<span class="dot abs" style="left:808px"></span>
<span class="dot on abs" style="left:833px"></span>
<span class="dot abs" style="left:859px"></span>

<main class="panel abs">
  <section class="feature" style="left:21px">
    <h2>WHAT IS KEYSTONER</h2>
    <div class="thumb" role="img" aria-label="Photo of a brick suburban house with a green lawn" style="background:linear-gradient(180deg,#8fb0d8,#a07a5c 55%,#5e7a3c)"></div>
    <p class="intro">If your business needs include Cleveland IT Services, consider locally-owned Harborline Systems.</p>
    <ul><li>Business process &amp; system automation</li><li>Network solutions</li><li>Managed services</li><li>Data services</li><li>Staff augmentation</li></ul>
    <div class="more orange">More Info</div>
  </section>
  <section class="feature" style="left:284px">
    <h2 style="top:15px">KEYSTONER DEMO</h2>
    <div class="thumb" role="img" aria-label="Photo of a Mediterranean villa among palm trees" style="background:linear-gradient(180deg,#cfd8df,#9c8468 55%,#4d5a34)"></div>
    <p class="intro" style="top:137px">Harborline Systems provides full-service web design, development and hosting solutions.</p>
    <ul><li>Database programming capabilities</li><li>Browser-based email access</li><li>Content management &amp; customization</li><li>Browser-based email access</li><li>Content management &amp; customization</li></ul>
    <div class="more green">More Info</div>
  </section>
  <section class="feature" style="left:546px">
    <h2>ORDER KEYSTONER</h2>
    <div class="thumb" role="img" aria-label="Photo of a new car owner holding up keys from the driver's seat" style="background:linear-gradient(90deg,#9aa7b4,#d9b38f 50%,#b3262a 80%,#5f6b78)"></div>
    <p class="intro" style="top:137px">If your business needs include Cleveland IT Services, consider locally-owned Harborline Systems.</p>
    <ul><li>Business process &amp; system automation</li><li>Network solutions</li><li>Managed services</li><li>Data services</li><li>Staff augmentation</li></ul>
    <div class="more green">More Info</div>
  </section>
</main>

<footer class="footer abs"></footer>
<div class="col-title abs" style="left:99px;top:885px">Testimonials</div>
<div class="col-rule abs" style="left:95px;top:913px;width:159px"></div>
<div class="vrule abs" style="left:278px;top:884px;height:270px"></div>
<p class="quote-text abs"><span class="qmark open">&ldquo;</span>Lorem ipsum dolor sit<br>amet, consectetur adipiscing elit.<br>Sed nec diam magna, a semper<br>est. Phasellus vulputate aliquam<br>elit vitae sagittis. Cras convallis<br>blandit ornare. Proin eget nibh at<br>odio ullamcorper molestie ut at<br>mauris. Integer non orci sapien, a<br>lobortis turpis. Nullam quis dui<br>ligula. Morbi luctus vestibulum elit,<br>in luctus cursus non.<span class="qmark close">&rdquo;</span></p>

<div class="col-title abs" style="left:299px;top:885px">Location Map</div>
<div class="col-rule abs" style="left:282px;top:913px;width:362px"></div>
<p class="map-text abs">Typesetting industry. Lorem Ipsum has been the industry's standard<br>dummy text ever since the 1500s, when an unknown</p>
<div class="map abs" role="img" aria-label="Street map of the office neighbourhood with a location marker"></div>
<div class="vrule abs" style="left:658px;top:884px;height:270px"></div>

<div class="col-title abs" style="left:682px;top:890px">Contact</div>
<div class="col-rule abs" style="left:671px;top:916px;width:185px"></div>
<div class="field abs" style="top:925px">Name</div>
<div class="field abs" style="top:949px">Email</div>
<div class="field abs" style="top:972px">Phone</div>
<div class="field abs" style="top:996px;height:37px;line-height:35px">Massege</div>
<div class="submit abs">Submit</div>
<p class="address abs">4870 Alder Lane #208<br>Brookvale OH 44990<br>440-555-KEYS<br><b>P:</b> 000 555 014 2290 &nbsp;/&nbsp; <b>P:</b> 000 555 014 2290</p>
<div class="world abs" role="img" aria-label="Faint world map decoration"></div>

<nav class="bottom-nav abs">
  <span>Home</span><span>|</span><span>Getting The Business</span><span>|</span><span>What is Keystoner</span><span>|</span><span>Peer Reviews</span><span>|</span><span>FAQ</span><span>|</span><span>About Us</span>
</nav>

</body>
</html>
```